Corporate Travel Technology Company needs new Business Card design

We need a new business card design to reflect our re-branded company. Our company is called tolvEn (pronounced tolvenn) and we provide Business Intelligence and mobile travel management solutions for the corporate travel industry. Our multinational customers use our solutions to manage large travel budgets and frequent travellers, as well as to save money and reduce risk. We'd like to see designs that use the blue and green palette as well as our corporate logo (attached below). The design should communicate innovation, insight, forward thinking, contemporary, trusted.

Target Market(s)

Large multinational corporates and Travel Agencies.

Industry/Entity Type

Business

Contact Information for Business Card

Rosalind Mercer
Chief Executive
tolvEn
Phone number - +61 (0)2 8134 2907
Email address - rosalind.mercer@tolven-example.com
Mobile number - +61 (0)438 516 702
www.tolven-example.com

Font styles to use
Other font styles liked:
• Please use font as close to corporate logo as possible

Colors
0255a3
0393ce
00a990
33b8a4
33a6d7
3176b5

Requirements
Must have
• Please include the words;
• Mobile Travel Management
• Accelerating Travel Business Insights
• Use corporate logo - although icon can be stylised if needed

```html
<!DOCTYPE html>
<html lang="en">
<head>
<meta charset="utf-8">
<title>tolvEn Business Card</title>
<link href="https://fonts.googleapis.com/css2?family=Open+Sans:wght@400;600;700&display=swap" rel="stylesheet">
<style>
  :root {
    --stage: #e9ebec;
    --slate: #5b6667;
    --sky: #00b2e8;
    --ink: #4b5758;
    --paper: #ffffff;
    --shadow: rgba(0, 0, 0, 0.18);
  }
  * { box-sizing: border-box; margin: 0; padding: 0; }
  html, body {
    width: 1200px;
    height: 950px;
    overflow: hidden;
    background: var(--stage);
    font-family: "Open Sans", Arial, sans-serif;
  }
  .canvas {
    width: 1200px;
    height: 950px;
    display: flex;
    flex-direction: column;
    align-items: center;
    justify-content: center;
    gap: 34px;
  }
  .card {
    width: 735px;
    height: 420px;
    box-shadow: 0 10px 26px var(--shadow);
    position: relative;
    overflow: hidden;
  }

  /* Back of card */
  .card-back {
    background: var(--slate);
    color: var(--paper);
  }
  .back-name {
    position: absolute;
    top: 130px;
    left: 0;
    right: 0;
    text-align: center;
    font-size: 60px;
    font-weight: 400;
    color: var(--paper);
  }
  .tagline {
    position: absolute;
    bottom: 46px;
    left: 0;
    right: 0;
    text-align: center;
    font-size: 16px;
    letter-spacing: 0.5px;
  }
  .tagline .sep {
    color: var(--sky);
    margin: 0 6px;
  }

  /* Front of card */
  .card-front {
    display: flex;
    background: var(--paper);
  }
  .contact-panel {
    width: 50%;
    background: var(--sky);
    color: var(--paper);
    padding: 96px 0 0 44px;
  }
  .person-name {
    font-size: 24px;
    font-weight: 700;
  }
  .person-title {
    font-size: 17px;
    margin-top: 2px;
  }
  .contact-list {
    list-style: none;
    margin-top: 30px;
  }
  .contact-list li {
    display: flex;
    align-items: center;
    gap: 12px;
    font-size: 15px;
    line-height: 28px;
    white-space: nowrap;
  }
  .contact-list svg {
    width: 15px;
    height: 15px;
    flex: none;
    fill: var(--paper);
  }
  .brand-panel {
    width: 50%;
    display: flex;
    align-items: center;
    justify-content: center;
  }
  .brand-name {
    font-size: 64px;
    font-weight: 400;
    color: var(--ink);
  }
</style>
</head>
<body>
<main class="canvas">
  <section class="card card-back">
    <p class="back-name">tolvEn</p>
    <p class="tagline">Mobile Travel Management<span class="sep">•</span>Accelerating Travel Business Insights</p>
  </section>

  <section class="card card-front">
    <div class="contact-panel">
      <h1 class="person-name">Rosalind Mercer</h1>
      <p class="person-title">Chief Executive</p>
      <ul class="contact-list">
        <li>
          <svg viewBox="0 0 16 16" aria-hidden="true"><path d="M1 5c0-2 2-3 7-3s7 1 7 3v1h-4V4.5H5V6H1zM3 7h10l1 7H2zm5 1.8a2.2 2.2 0 1 0 0 4.4 2.2 2.2 0 0 0 0-4.4z"/></svg>
          +61 (0)2 8134 2907
        </li>
        <li>
          <svg viewBox="0 0 16 16" aria-hidden="true"><path d="M4 0h8a1 1 0 0 1 1 1v14a1 1 0 0 1-1 1H4a1 1 0 0 1-1-1V1a1 1 0 0 1 1-1zm1 2v10h6V2zm3 11a1 1 0 1 0 0 2 1 1 0 0 0 0-2z"/></svg>
          +61 (0)438 516 702
        </li>
        <li>
          <svg viewBox="0 0 16 16" aria-hidden="true"><path d="M1 3h14v1L8 9 1 4zm0 2.5 7 5 7-5V13H1z"/></svg>
          rosalind.mercer@tolven-example.com
        </li>
        <li>
          <svg viewBox="0 0 16 16" aria-hidden="true"><path d="M8 0a8 8 0 1 0 0 16A8 8 0 0 0 8 0zm0 1.5c.9 0 2 2 2.3 5.5H5.7C6 3.5 7.1 1.5 8 1.5zM1.6 7h2.6c.1-2 .5-3.7 1.1-4.8A6.5 6.5 0 0 0 1.6 7zm0 2a6.5 6.5 0 0 0 3.7 4.8C4.7 12.7 4.3 11 4.2 9zm4.1 0h4.6c-.3 3.5-1.4 5.5-2.3 5.5S6 12.5 5.7 9zm6.1 0h2.6a6.5 6.5 0 0 1-3.7 4.8c.6-1.1 1-2.8 1.1-4.8zm2.6-2h-2.6c-.1-2-.5-3.7-1.1-4.8A6.5 6.5 0 0 1 14.4 7z"/></svg>
          www.tolven-example.com
        </li>
      </ul>
    </div>
    <div class="brand-panel">
      <span class="brand-name">tolvEn</span>
    </div>
  </section>
</main>
</body>
</html>
```